One of a kind service business!

We are the only ocean freight auditing company in the entire world that does what we do. We provide a innovative service in auditing our clients invoices for billing errors as it relates to the import and export of their products anywhere in the world. We'd like to retain the current logo - but we are open to any interesting concepts that can complete the card.

Target Market(s)

C-Level and Senior Financial executives

Industry/Entity Type

Auditing

Requirements
Must have

• ONE SIDED ONLY
Should not have
• no cartoonish images

```html
<!DOCTYPE html>
<html lang="en">
<head>
<meta charset="utf-8">
<title>Tidemark Audit – Business Card</title>
<link rel="stylesheet" href="https://fonts.googleapis.com/css2?family=Arimo:wght@400;700&display=swap">
<style>
  :root {
    --page-bg: #e6e6e6;
    --card-white: #ffffff;
    --ocean-blue: #15609a;
    --brand-blue: #1b6fae;
    --ink: #2b2b2b;
    --night: #211d1c;
    --light-text: #ffffff;
  }
  * { margin: 0; padding: 0; box-sizing: border-box; }
  html, body { width: 1200px; height: 944px; overflow: hidden; background: var(--page-bg); }
  body { font-family: "Arimo", Arial, sans-serif; position: relative; }

  .business-card {
    position: absolute;
    left: 150px; top: 213px;
    width: 900px; height: 518px;
    background: var(--card-white);
    border-radius: 26px;
    overflow: hidden;
    box-shadow: 0 10px 24px rgba(0,0,0,0.25);
  }
  .card-waves { position: absolute; inset: 0; }

  .brand {
    position: absolute; left: 47px; top: 72px;
    display: flex; align-items: center; gap: 14px;
  }
  .brand-mark { width: 22px; height: 22px; background: var(--brand-blue); }
  .brand-name {
    font-size: 56px; font-weight: 700; color: var(--brand-blue);
    letter-spacing: 1px; line-height: 1;
  }

  .contact-list {
    position: absolute; left: 60px; top: 188px;
    list-style: none; color: var(--ink); font-size: 24px; line-height: 32px;
  }
  .contact-list li { display: flex; align-items: flex-start; }
  .contact-list .icon { width: 20px; height: 20px; margin: 6px 16px 0 0; flex: none; fill: var(--ocean-blue); }
  .contact-list .address { margin-bottom: 14px; }
  .contact-list .address span { display: block; }
  .contact-list .phones li { line-height: 31px; }

  .holder {
    position: absolute; left: 612px; top: 428px; width: 240px;
    text-align: center; color: var(--light-text);
  }
  .holder-name { font-size: 33px; font-weight: 400; line-height: 1.1; }
  .holder-role { font-size: 21px; margin-top: 6px; }
</style>
</head>
<body>
  <article class="business-card">
    <svg class="card-waves" viewBox="0 0 900 518" width="900" height="518" aria-hidden="true">
      <path d="M553 0 C600 80 640 170 600 270 C560 360 460 420 445 518 L900 518 L900 0 Z" fill="var(--ocean-blue)"/>
      <path d="M657 0 C700 90 670 200 600 280 C560 330 530 420 531 518 L900 518 L900 0 Z" fill="var(--night)"/>
    </svg>

    <div class="brand">
      <span class="brand-mark"></span>
      <span class="brand-name">Tidemark Audit</span>
    </div>

    <ul class="contact-list">
      <li class="address">
        <svg class="icon" viewBox="0 0 20 20"><path d="M10 1 L1 10 H4 V19 H8 V13 H12 V19 H16 V10 H19 Z"/></svg>
        <div>
          <span>Harbor Business Center</span>
          <span>Lindenova 18, Prague</span>
          <span>Czech Republic 11000</span>
        </div>
      </li>
      <li>
        <ul class="phones" style="list-style:none">
          <li><svg class="icon" viewBox="0 0 20 20"><path d="M5 2 L8 2 L9 7 L7 8.5 C8 11 9.5 12.5 12 13.5 L13.5 11.5 L18 12.5 L18 16 C18 17 17 18 16 18 C8 18 2 12 2 4 C2 3 3 2 5 2 Z"/></svg>+420 555 010 141</li>
          <li><svg class="icon" viewBox="0 0 20 20"><rect x="5" y="1" width="10" height="18" rx="2"/><rect x="7" y="3.5" width="6" height="8" fill="#fff"/></svg>+420 555 020 257</li>
          <li><svg class="icon" viewBox="0 0 20 20"><path d="M5 2 L8 2 L9 7 L7 8.5 C8 11 9.5 12.5 12 13.5 L13.5 11.5 L18 12.5 L18 16 C18 17 17 18 16 18 C8 18 2 12 2 4 C2 3 3 2 5 2 Z"/></svg>+1 555 014 7902 - USA</li>
          <li><svg class="icon" viewBox="0 0 20 20"><rect x="5" y="2" width="10" height="6"/><rect x="1" y="8" width="18" height="8" rx="2"/><rect x="5" y="14" width="10" height="4" fill="#fff" stroke="var(--ocean-blue)" stroke-width="1.5"/></svg>+420 555 030 200</li>
          <li><svg class="icon" viewBox="0 0 20 20"><circle cx="10" cy="10" r="9"/><path d="M1 10 H19 M10 1 C6 5 6 15 10 19 M10 1 C14 5 14 15 10 19" stroke="#fff" stroke-width="1.3" fill="none"/></svg>www.tidemarkaudit.net</li>
          <li><svg class="icon" viewBox="0 0 20 20"><rect x="1" y="4" width="18" height="13" rx="1.5"/><path d="M1.5 5 L10 12 L18.5 5" stroke="#fff" stroke-width="1.6" fill="none"/></svg>danielm@tidemarkaudit.net</li>
        </ul>
      </li>
    </ul>

    <div class="holder">
      <p class="holder-name">Daniel Moreau</p>
      <p class="holder-role">CEO</p>
    </div>
  </article>
</body>
</html>
```